Need a new company business card

I am looking for a new company business card. Front and back. With information on it as per below. Card should be professional. Yet clever. Simple. Modern design. Pim card, traditional size. OK with say, all black or all red backside.

Varnholt is an indie, bootstrapped magazine advancing the work of intersectional feminists busting their buts to create a just world through the power of enterprise and innovation.

Varnholt is the home and voice of entrepreneurial feminism and feminist innovators worldwide. Entrepreneurial feminists are people (of all genders) who see inequality as an innovation priority. They work to advance gender equity and/or who strive to integrate and practice feminist principles, pedagogy, values into their innovation and entrepreneurship work.
We are committed to this space being trans and queer inclusive, anti-racist, intersectional, brave, and safe. We welcome all allies. We value learning, edgy but civil discourse and integrative thinking skills.

Target Market(s)

feminists, business owners,

Industry/Entity Type

Publishing Company

Contact Information for Business Card

RD Tolliver
Founder/Publisher
4-237 Ashgrove Lane, Toronto, ON
M4T 2K8
publisher@varnholt.com
416-552-3019
www.varnholt.com

Font styles to use
Serif
Other font styles liked:
• Myriad Pro

Colors
ec1f27
000000
ffffff

Requirements
Must have
• logo
• use red, black white colours only.
Nice to have
• use the compass in pattern or creatively but not too busy please
Should not have
• Should not be too busy. Elegant.

```html
<!DOCTYPE html>
<html lang="en">
<head>
<meta charset="utf-8">
<title>Varnholt business card</title>
<link href="https://fonts.googleapis.com/css2?family=Open+Sans:wght@700&family=Roboto:wght@400;500&family=Merriweather:wght@400&display=swap" rel="stylesheet">
<style>
  :root{
    --brand-red:#ec1f27;
    --ink:#2b2b2b;
    --muted:#555555;
    --paper:#f6f6f4;
    --white:#ffffff;
    --tint:#f6d3d3;
    --stage:#e4e2df;
  }
  *{margin:0;padding:0;box-sizing:border-box}
  html,body{width:1200px;height:886px;overflow:hidden;background:var(--stage)}
  .canvas{position:relative;width:1200px;height:886px}
  .card{position:absolute;width:525px;height:300px;overflow:hidden;box-shadow:0 6px 18px rgba(0,0,0,.18)}
  .card--front{left:70px;top:90px;background:var(--brand-red)}
  .card--back{left:605px;top:490px;background:var(--paper)}

  .decor{position:absolute;border-radius:50%}
  .card--front .decor{right:40px;top:-20px;width:230px;height:230px;background:var(--white)}
  .card--back .decor{right:20px;top:-10px;width:240px;height:240px;background:var(--tint)}

  .wordmark{position:absolute;display:flex;flex-direction:column}
  .wordmark__row{display:flex;align-items:flex-start;gap:6px}
  .wordmark__name{font-family:"Open Sans",sans-serif;font-weight:700;font-size:50px;line-height:1;letter-spacing:-1px}
  .wordmark__badge{width:12px;height:12px;border-radius:50%;margin-top:2px}
  .tagline{font-family:"Merriweather",serif;font-size:7px;letter-spacing:.6px;text-transform:uppercase;margin-top:4px}

  .card--front .wordmark{left:34px;bottom:34px;color:var(--white)}
  .card--front .wordmark__badge{border:1.5px solid var(--white)}
  .site{font-family:"Merriweather",serif;font-size:11px;letter-spacing:5px;margin-top:8px}

  .card--back .wordmark{left:36px;top:60px;color:var(--ink)}
  .card--back .wordmark__badge{border:1.5px solid var(--ink)}

  .person{position:absolute;right:34px;top:120px;text-align:right;font-family:"Roboto",sans-serif}
  .person__name{font-size:19px;font-weight:500;color:var(--ink);text-transform:uppercase}
  .person__role{font-size:14px;color:var(--brand-red)}
  .tab{position:absolute;right:0;top:118px;width:14px;height:38px;background:var(--brand-red)}

  .contact{position:absolute;left:40px;bottom:28px;font-family:"Roboto",sans-serif;font-size:12.5px;color:var(--muted);line-height:1.35}
  .contact__address{margin-bottom:10px}
  .contact__line{display:flex;align-items:center;gap:8px}
  .contact__line svg{width:11px;height:11px;fill:var(--ink)}
</style>
</head>
<body>
<main class="canvas">
  <section class="card card--front" aria-label="Card front">
    <div class="decor" aria-hidden="true"></div>
    <div class="wordmark">
      <div class="wordmark__row">
        <span class="wordmark__name">Varnholt</span>
        <span class="wordmark__badge" aria-hidden="true"></span>
      </div>
      <span class="tagline">Independent journal of equal enterprise</span>
      <span class="site">www.varnholt.com</span>
    </div>
  </section>

  <section class="card card--back" aria-label="Card back">
    <div class="decor" aria-hidden="true"></div>
    <div class="wordmark">
      <div class="wordmark__row">
        <span class="wordmark__name">Varnholt</span>
        <span class="wordmark__badge" aria-hidden="true"></span>
      </div>
      <span class="tagline">Independent journal of equal enterprise</span>
    </div>
    <div class="tab" aria-hidden="true"></div>
    <div class="person">
      <p class="person__name">RD Tolliver</p>
      <p class="person__role">Founder/Publisher</p>
    </div>
    <div class="contact">
      <p class="contact__address">4-237 Ashgrove Lane<br>Toronto, ON, M4T 2K8</p>
      <p class="contact__line"><svg viewBox="0 0 24 24" aria-hidden="true"><path d="M6.6 10.8a15.1 15.1 0 0 0 6.6 6.6l2.2-2.2a1 1 0 0 1 1-.25 11.4 11.4 0 0 0 3.6.6 1 1 0 0 1 1 1V20a1 1 0 0 1-1 1A17 17 0 0 1 3 4a1 1 0 0 1 1-1h3.5a1 1 0 0 1 1 1c0 1.25.2 2.45.6 3.6a1 1 0 0 1-.25 1z"/></svg>416-552-3019</p>
      <p class="contact__line"><svg viewBox="0 0 24 24" aria-hidden="true"><path d="M2 5h20v14H2zm2 2v.5l8 5 8-5V7l-8 5z"/></svg>publisher@varnholt.com</p>
      <p class="contact__line"><svg viewBox="0 0 24 24" aria-hidden="true"><circle cx="12" cy="12" r="10"/></svg>www.varnholt.com</p>
    </div>
  </section>
</main>
</body>
</html>
```